Dynamic Business Card for Sports Supplements Company

Hi! I'm looking for an awesome business card to match my existing sports supplement company. I have uploaded my current company logo and screenshot of the front page of my website.

I would like to have something dynamic and interesting and utilize the colors in the website - the reds and purples

The business card should be double sided and focus on a unique eye-catching design on the back and include all the relevant company info.

Most importantly, it should say somewhere: "Sign up on our website for a coupon code."

Target Market(s)

Mostly for women gym goers but it shouldn't be too feminine. It should be in keeping with the website design. It should flow and clearly be connected to it

Industry/Entity Type

Business

Contact Information for Business Card

Lorraine K. Vestal
CEO
LVestal@Quorvanexco.com
www.quorvanexco.com
555.417.3820
P.O. Box 47315
Fenwick, Oregon 00000

Sign up on our website for a coupon code

Font styles to use
Serif
Sans Serif
Other font styles liked:
• Novecento font family and "Quorvanex" is in AR Destine font

Requirements
Must have
• One side should be a bold Quorvanex logo design. Even just the symbol itself may be o.k. (see attached file)

```html
<!DOCTYPE html>
<html lang="en">
<head>
<meta charset="utf-8">
<title>Quorvanex Business Card</title>
<link href="https://fonts.googleapis.com/css2?family=Saira:ital,wght@0,400;0,600;0,700;1,400&display=swap" rel="stylesheet">
<style>
  :root {
    --page-bg: #e4e4e4;
    --card-bg: #ffffff;
    --brand-red: #e1252b;
    --brand-navy: #2e2b6f;
    --text-gray: #555555;
    --ghost-gray: #ececec;
    --card-shadow: 0 6px 18px rgba(0, 0, 0, 0.18);
  }
  * { box-sizing: border-box; margin: 0; padding: 0; }
  html, body {
    width: 1200px;
    height: 1000px;
    overflow: hidden;
    background: var(--page-bg);
    font-family: "Saira", "Arial", sans-serif;
  }
  .card-set {
    position: absolute;
    top: 353px;
    left: 60px;
    display: flex;
    gap: 40px;
  }
  .card {
    position: relative;
    width: 520px;
    height: 294px;
    background: var(--card-bg);
    box-shadow: var(--card-shadow);
    overflow: hidden;
  }

  /* Back side: contact details */
  .card-back { padding: 36px 0 0 36px; color: var(--text-gray); }
  .contact-name {
    color: var(--brand-red);
    font-weight: 700;
    font-size: 15px;
    letter-spacing: 0.5px;
    line-height: 1;
  }
  .contact-title { font-size: 11px; margin-top: 3px; }
  .contact-list { list-style: none; margin-top: 16px; }
  .contact-list li {
    display: flex;
    align-items: center;
    gap: 8px;
    font-size: 11.5px;
    line-height: 17px;
  }
  .contact-list svg { width: 10px; height: 10px; fill: var(--brand-red); flex: none; }
  .web-highlight { color: var(--brand-red); }
  .contact-address {
    display: flex;
    gap: 8px;
    margin-top: 14px;
    font-size: 11.5px;
    line-height: 16px;
  }
  .contact-address svg { width: 10px; height: 10px; fill: var(--brand-red); margin-top: 3px; flex: none; }
  .coupon-note {
    margin-top: 22px;
    font-style: italic;
    font-size: 11.5px;
    letter-spacing: 0.4px;
  }
  .ghost-wordmark {
    position: absolute;
    left: 34px;
    bottom: -18px;
    font-size: 58px;
    font-weight: 700;
    letter-spacing: 3px;
    color: var(--ghost-gray);
    line-height: 1;
  }

  /* Front side: brand name */
  .card-front {
    display: flex;
    align-items: center;
    justify-content: center;
  }
  .brand-lockup { display: flex; align-items: center; gap: 12px; }
  .brand-mark { width: 30px; height: 30px; background: var(--brand-red); }
  .brand-name {
    font-weight: 700;
    font-size: 40px;
    letter-spacing: 2px;
    color: var(--brand-navy);
    line-height: 1;
  }
</style>
</head>
<body>
  <main class="card-set">
    <section class="card card-back" aria-label="Card back with contact details">
      <h1 class="contact-name">LORRAINE K. VESTAL</h1>
      <p class="contact-title">CEO</p>
      <ul class="contact-list">
        <li>
          <svg viewBox="0 0 10 10" aria-hidden="true"><path d="M2 1h2l1 2-1.3 1a5 5 0 0 0 2.3 2.3L7 5l2 1v2a1 1 0 0 1-1 1A7.5 7.5 0 0 1 1 2a1 1 0 0 1 1-1z"/></svg>
          555.417.3820
        </li>
        <li>
          <svg viewBox="0 0 10 10" aria-hidden="true"><path d="M0 2h10v6H0z M0.6 2.4 5 5.6l4.4-3.2" stroke="#fff" stroke-width="0.8"/></svg>
          LVestal@Quorvanexco.com
        </li>
        <li>
          <svg viewBox="0 0 10 10" aria-hidden="true"><circle cx="6" cy="4" r="3" fill="none" stroke="#e1252b" stroke-width="1.4"/><path d="M3.8 5.8 0.8 8.8" stroke="#e1252b" stroke-width="1.8"/></svg>
          <span>www.<span class="web-highlight">quorvanexco</span>.com</span>
        </li>
      </ul>
      <div class="contact-address">
        <svg viewBox="0 0 10 10" aria-hidden="true"><path d="M10 0 0 4l4 1.5L5.5 10z"/></svg>
        <p>P.O. Box 47315 Fenwick,<br>Oregon 00000</p>
      </div>
      <p class="coupon-note">SIGN UP ON OUR WEBSITE FOR A COUPON CODE</p>
      <div class="ghost-wordmark" aria-hidden="true">QUORVANEX</div>
    </section>

    <section class="card card-front" aria-label="Card front with brand name">
      <div class="brand-lockup">
        <span class="brand-mark" aria-hidden="true"></span>
        <span class="brand-name">QUORVANEX</span>
      </div>
    </section>
  </main>
</body>
</html>
```